Fitness Business Card Design Needed

We are looking for a business card design that stands out but is also simple and unique. I like the idea of on one side using the picture of myself with my logo at my feet. I love the texture on the business card so please take that into account when designing. Then on the other side having my contact details. I want it to be clean, modern, and pretty. I am open to designs that allow spot gloss or gold foiling.

Contact Information for Business Card

Space for Name, Phone number, email, and website

```html
<!DOCTYPE html>
<html lang="en">
<head>
<meta charset="utf-8">
<title>Petite Power Fitness – Business Card</title>
<link href="https://fonts.googleapis.com/css2?family=Great+Vibes&family=Montserrat:wght@400;500&display=swap" rel="stylesheet">
<style>
  :root {
    --backdrop: #3a3a3c;
    --card: #161616;
    --card-edge: #222222;
    --gold: #c9a45c;
    --gold-light: #e2c68a;
    --white: #f4f4f4;
    --rule: #d8d8d8;
    --photo-warm: #c9a48a;
    --photo-dark: #2a2220;
  }
  * { margin: 0; padding: 0; box-sizing: border-box; }
  html, body {
    width: 1200px;
    height: 900px;
    overflow: hidden;
    background: var(--backdrop);
  }
  .canvas {
    position: relative;
    width: 1200px;
    height: 900px;
  }
  .card {
    position: absolute;
    top: 100px;
    width: 400px;
    height: 700px;
    background: linear-gradient(160deg, var(--card-edge) 0%, var(--card) 55%, #101010 100%);
    border-radius: 4px;
    box-shadow: 0 10px 30px rgba(0,0,0,0.45);
    overflow: hidden;
  }
  .card--brand { left: 170px; }
  .card--contact { left: 630px; }

  /* Brand side */
  .brand-lockup {
    position: absolute;
    left: 0;
    right: 0;
    top: 430px;
    display: flex;
    flex-direction: column;
    align-items: center;
    gap: 22px;
  }
  .brand-mark {
    width: 56px;
    height: 56px;
    border: 2px solid var(--gold);
  }
  .brand-name {
    font-family: "Montserrat", sans-serif;
    font-weight: 400;
    font-size: 22px;
    letter-spacing: 5px;
    color: var(--gold);
    text-align: center;
    line-height: 1.5;
  }

  /* Contact side */
  .portrait {
    position: absolute;
    left: 90px;
    top: 40px;
    width: 220px;
    height: 220px;
  }
  .identity {
    position: absolute;
    top: 282px;
    left: 0;
    right: 0;
    text-align: center;
  }
  .identity__name {
    font-family: "Great Vibes", cursive;
    font-size: 64px;
    line-height: 1;
    color: var(--gold);
  }
  .identity__title {
    font-family: "Montserrat", sans-serif;
    font-weight: 400;
    font-size: 30px;
    color: var(--white);
    margin-top: 6px;
  }
  .contact-table {
    position: absolute;
    left: 0;
    right: 0;
    top: 440px;
    border-top: 2px solid var(--rule);
  }
  .contact-row {
    display: flex;
    height: 76px;
    border-bottom: 2px solid var(--rule);
  }
  .contact-row__icon {
    width: 84px;
    display: flex;
    align-items: center;
    justify-content: center;
    border-right: 2px solid var(--rule);
  }
  .contact-row__icon svg { width: 26px; height: 26px; }
  .contact-row__text {
    flex: 1;
    display: flex;
    align-items: center;
    padding-left: 28px;
    font-family: "Montserrat", sans-serif;
    font-weight: 400;
    font-size: 20px;
    color: var(--gold-light);
  }
</style>
</head>
<body>
<main class="canvas">

  <section class="card card--brand" aria-label="Card front">
    <div class="brand-lockup">
      <div class="brand-mark"></div>
      <div class="brand-name">PETITE POWER<br>FITNESS</div>
    </div>
  </section>

  <section class="card card--contact" aria-label="Card back">
    <svg class="portrait" viewBox="0 0 220 220">
      <defs>
        <linearGradient id="portrait-tone" x1="0" y1="0" x2="0" y2="1">
          <stop offset="0" stop-color="var(--photo-dark)"/>
          <stop offset="0.5" stop-color="var(--photo-warm)"/>
          <stop offset="1" stop-color="#b8553f"/>
        </linearGradient>
      </defs>
      <polygon points="110,12 208,110 110,208 12,110" fill="url(#portrait-tone)" role="img" aria-label="Portrait photo of the trainer"/>
      <polygon points="110,6 214,110 110,214 6,110" fill="none" stroke="var(--gold)" stroke-width="5"/>
    </svg>

    <div class="identity">
      <div class="identity__name">Your Name</div>
      <div class="identity__title">Your Title</div>
    </div>

    <div class="contact-table">
      <div class="contact-row">
        <div class="contact-row__icon">
          <svg viewBox="0 0 24 24" aria-hidden="true"><path fill="var(--white)" d="M6.6 10.8c1.4 2.8 3.8 5.1 6.6 6.6l2.2-2.2c.3-.3.7-.4 1-.2 1.1.4 2.3.6 3.6.6.6 0 1 .4 1 1V20c0 .6-.4 1-1 1C10.6 21 3 13.4 3 4c0-.6.4-1 1-1h3.5c.6 0 1 .4 1 1 0 1.3.2 2.5.6 3.6.1.3 0 .7-.2 1L6.6 10.8z"/></svg>
        </div>
        <div class="contact-row__text">123-456-2100</div>
      </div>
      <div class="contact-row">
        <div class="contact-row__icon">
          <svg viewBox="0 0 24 24" aria-hidden="true"><rect x="2" y="5" width="20" height="14" fill="var(--white)"/><path d="M2 5l10 8 10-8" fill="none" stroke="var(--card)" stroke-width="1.6"/></svg>
        </div>
        <div class="contact-row__text">youremail@mailbox.com</div>
      </div>
      <div class="contact-row">
        <div class="contact-row__icon">
          <svg viewBox="0 0 24 24" aria-hidden="true"><circle cx="12" cy="12" r="10" fill="none" stroke="var(--white)" stroke-width="2"/><ellipse cx="12" cy="12" rx="4" ry="10" fill="none" stroke="var(--white)" stroke-width="1.6"/><path d="M2 12h20" stroke="var(--white)" stroke-width="1.6"/></svg>
        </div>
        <div class="contact-row__text">www.yourwebsite.com</div>
      </div>
    </div>
  </section>

</main>
</body>
</html>
```